Redesign of business card for Cedar Ridge Mechanical

We are looking for a new design for our business cards for Cedar Ridge Mechanical. We are a plumbing & HVAC construction company, operating on the West Coast of Canada and USA. Logo attached.
Industry/Entity Type
Construction - Plumbing & HVAC
Contact Information for Business Card
Name, address, phone numbers, email, website address
Look and feel
Each slider illustrates characteristics of the customer's brand and the style your logo design should communicate.

```html
<!DOCTYPE html>
<html lang="en">
<head>
<meta charset="UTF-8">
<title>Cedar Ridge Mechanical – Business Card</title>
<link rel="stylesheet" href="https://fonts.googleapis.com/css2?family=Poppins:wght@300;400;500;600&display=swap">
<style>
  :root {
    --page-bg: #222224;
    --card-bg: #1b1b1d;
    --card-edge: #111113;
    --ink-light: #ffffff;
    --ink-muted: #d8d8d8;
    --emboss: #2e2e31;
  }
  * { box-sizing: border-box; margin: 0; padding: 0; }
  html, body {
    width: 1200px; height: 780px; overflow: hidden;
    background: var(--page-bg);
    font-family: "Poppins", sans-serif;
  }
  .canvas {
    position: relative; width: 1200px; height: 780px;
    display: flex; align-items: center; justify-content: center; gap: 40px;
  }
  .card {
    position: relative; width: 520px; height: 300px;
    background: var(--card-bg);
    box-shadow: 0 0 0 1px var(--card-edge), 0 18px 40px rgba(0,0,0,.45);
  }

  /* Front: person and contact details */
  .holder {
    position: absolute; left: 26px; bottom: 26px;
    writing-mode: vertical-rl; transform: rotate(180deg);
    color: var(--ink-light);
  }
  .holder-name { font-size: 24px; line-height: 1.1; letter-spacing: .5px; }
  .holder-name .first { font-weight: 600; }
  .holder-name .last { font-weight: 300; }
  .holder-title { font-size: 10.5px; font-weight: 400; margin-right: 4px; letter-spacing: .4px; }

  .brand {
    position: absolute; top: 44px; right: 36px;
    display: flex; align-items: center; gap: 10px;
    color: var(--ink-light);
    font-size: 16px; font-weight: 500; letter-spacing: .3px;
  }
  .brand-mark { width: 16px; height: 16px; background: var(--ink-light); }

  .contact {
    position: absolute; right: 36px; bottom: 28px;
    list-style: none; text-align: right;
    color: var(--ink-muted); font-size: 12px; font-weight: 400; line-height: 1.6;
  }
  .contact li { display: flex; justify-content: flex-end; align-items: center; gap: 8px; }
  .contact .address { margin-bottom: 6px; }
  .contact svg { width: 12px; height: 12px; flex: none; }

  /* Back: brand name */
  .card-back { display: flex; align-items: center; justify-content: center; }
  .brand-large {
    display: flex; align-items: center; gap: 16px;
    color: var(--emboss);
    font-size: 30px; font-weight: 500; letter-spacing: .5px;
  }
  .brand-large .brand-mark { width: 26px; height: 26px; background: var(--emboss); }
</style>
</head>
<body>
<main class="canvas">
  <section class="card card-front">
    <div class="holder">
      <p class="holder-name"><span class="first">Marta</span> <span class="last">Velasco</span></p>
      <p class="holder-title">Founder &amp; CEO</p>
    </div>

    <div class="brand">
      <span class="brand-mark"></span>
      <span class="brand-name">Cedar Ridge Mechanical</span>
    </div>

    <ul class="contact">
      <li class="address">1480 Harbor Ln. Suite 300<br>Portland, OR 97205</li>
      <li>(503) 555-0147
        <svg viewBox="0 0 24 24" aria-hidden="true"><path fill="#fff" d="M6.6 10.8a15.1 15.1 0 0 0 6.6 6.6l2.2-2.2a1 1 0 0 1 1-.25 11.4 11.4 0 0 0 3.6.57 1 1 0 0 1 1 1V20a1 1 0 0 1-1 1A17 17 0 0 1 3 4a1 1 0 0 1 1-1h3.5a1 1 0 0 1 1 1c0 1.25.2 2.45.57 3.57a1 1 0 0 1-.25 1z"/></svg>
      </li>
      <li>info@cedarridgemech.com
        <svg viewBox="0 0 24 24" aria-hidden="true"><rect x="2" y="5" width="20" height="14" rx="2" fill="none" stroke="#fff" stroke-width="2"/><path d="M3 6l9 7 9-7" fill="none" stroke="#fff" stroke-width="2"/></svg>
      </li>
      <li>www.cedarridgemech.com
        <svg viewBox="0 0 24 24" aria-hidden="true"><circle cx="12" cy="12" r="9.5" fill="none" stroke="#fff" stroke-width="2"/><path d="M2.5 12h19M12 2.5c3 3 3 16 0 19M12 2.5c-3 3-3 16 0 19" fill="none" stroke="#fff" stroke-width="1.6"/></svg>
      </li>
    </ul>
  </section>

  <section class="card card-back">
    <div class="brand-large">
      <span class="brand-mark"></span>
      <span class="brand-name">Cedar Ridge Mechanical</span>
    </div>
  </section>
</main>
</body>
</html>
```